Events publishing website

Have increased the budget for Coded website design. Thanks
-
We need a wordpress website for events publishing. The website will be using all different kinds of events (social, business, music etc). The website should allow user to submit the new events. the new events will be published after admin reviewed.
Key menu items & requirements
- New Events (1-show picture, short description & start/end date. User can view more details in another page. 2-have categories, such as locations, free/ticked, event type etc. 3 - allow user to share the events in social website)
- Event organizer list (show the full list and most popular event organizers. users can view the list by categories, similar to above)
- events establishments (allow user to publish events related informations such as equipments, venue informations etc)
- discussion forum
Key functions
-registration page (new users should fill name, location, normal users or event organizer, types of event organizer etc)
-allow user to change locations to view different events
-search function
The functions should be similar to the following, the design should not. The website should not look like a proper website.
http://www.plavorgatherings.example
Reason: Hi All, have extended few days to allow some changes to be made for current design. Thanks

```html
<!DOCTYPE html>
<html lang="en">
<head>
<meta charset="utf-8">
<title>Events</title>
<link href="https://fonts.googleapis.com/css2?family=Cuprum:wght@400;700&family=Open+Sans:wght@400;600&display=swap" rel="stylesheet">
<style>
:root{
  --teal:#2f6e66;
  --teal-dark:#1f4f49;
  --teal-light:#4d8d84;
  --orange:#ef8a12;
  --orange-dark:#c96e08;
  --ink:#1d1d1d;
  --muted:#444;
  --paper:#ffffff;
  --bg:#e9e7df;
  --rule:#b8b8b8;
}
*{box-sizing:border-box;margin:0;padding:0}
html,body{width:1200px;height:2261px;overflow:hidden}
body{position:relative;background:radial-gradient(ellipse at 50% 20%,#f7f6f1 0%,#e6e3d9 70%,#dcd8cc 100%);font-family:"Open Sans",sans-serif;color:var(--ink)}
.abs{position:absolute}
.topbar{left:0;top:0;width:1200px;height:35px;background:#111;color:#eee;font-size:12px;display:flex;align-items:center;padding-left:34px;gap:10px;letter-spacing:.3px}
.topbar .sep{color:#888}
.brand{left:45px;top:70px;font-family:"Cuprum",sans-serif;color:var(--teal);font-size:44px;line-height:1}
.slogan{left:47px;top:116px;font-family:"Cuprum",sans-serif;color:var(--teal);font-size:18px}
.account{top:62px;right:50px;display:flex;gap:26px;font-family:"Cuprum",sans-serif;font-size:17px;color:var(--teal-dark)}
.account span{display:flex;align-items:center;gap:6px}
.search{left:835px;top:110px;width:300px;height:40px;background:#fff;border:1px solid #ccc;border-radius:4px 0 0 4px;font-size:14px;color:#555;padding:10px 12px}
.search-go{left:1137px;top:110px;width:38px;height:40px;background:var(--orange);border-radius:4px;color:#fff;font-family:"Cuprum",sans-serif;font-size:18px;text-align:center;line-height:40px}
.nav{left:35px;top:170px;width:1144px;height:67px;background:linear-gradient(#4a8a82,#2c6760);border-radius:6px 6px 0 0;display:flex;font-family:"Cuprum",sans-serif;font-size:21px;color:#fff}
.nav span{padding:0 32px;line-height:67px;border-right:1px solid #1e4d47;box-shadow:1px 0 0 #5c9a92}
.hero{left:35px;top:238px;width:1144px;height:357px;background:linear-gradient(90deg,#4b5a7a 0%,#2b2a38 35%,#5a2a20 60%,#c2531a 80%,#7a1f16 100%)}
.hero-arrow{top:375px;width:32px;height:48px;background:#f2f2f2;border:1px solid #ccc;color:#777;font-size:26px;text-align:center;line-height:44px}
.panel{left:35px;top:595px;width:1144px;height:1339px;background:var(--paper)}
.filter{left:47px;top:603px;width:788px;height:54px;background:var(--orange);display:flex;align-items:center;padding:0 12px;font-family:"Cuprum",sans-serif;font-size:21px;color:#fff}
.filter .field{background:#fff;border-radius:12px;height:24px;margin:0 12px 0 6px}
.filter .go{margin-left:auto;background:var(--orange-dark);border-radius:3px;width:56px;height:30px;font-size:18px;text-align:center;line-height:30px}
.total{left:64px;top:674px;font-family:"Cuprum",sans-serif;font-size:20px}
.event{left:61px;width:760px;height:180px}
.event .photo{position:absolute;left:0;top:0;width:243px;height:174px;border:4px solid #fff;box-shadow:0 0 3px #888}
.event .body{position:absolute;left:266px;top:6px;width:494px}
.event h3{font-family:"Cuprum",sans-serif;font-weight:400;font-size:21px;margin-bottom:4px}
.event p{font-size:12px;line-height:19px;letter-spacing:-.1px}
.event .line{font-size:13px;margin-top:8px}
.share{display:flex;align-items:center;gap:6px;font-size:13px;margin-top:7px}
.share i{display:inline-block;width:26px;height:26px;border-radius:3px}
.divider{left:59px;width:756px;border-top:1px dashed var(--rule)}
.pager{left:590px;top:1896px;display:flex;align-items:center;gap:12px;font-size:15px}
.pager .on{width:24px;height:24px;border-radius:50%;background:var(--teal);color:#fff;text-align:center;line-height:24px}
.pager-rule{left:70px;top:1887px;width:745px;border-top:1px solid #cfdcda}
.side{left:847px;top:603px;width:325px;height:1315px;border-left:1px solid #ddd}
.side h2{position:absolute;left:0;top:0;width:325px;height:51px;background:linear-gradient(#f3f7f6,#dde8e6);border-bottom:2px solid #c6d6d3;font-family:"Cuprum",sans-serif;font-weight:400;font-size:24px;color:var(--teal-dark);padding:10px 18px}
.card{left:860px;width:295px}
.card .photo{width:295px;height:127px;border:4px solid #fff;box-shadow:0 0 3px #888}
.card h4{font-family:"Cuprum",sans-serif;font-weight:400;font-size:18px;color:var(--teal-dark);margin-top:13px}
.card .meta{font-size:12px;margin-top:5px}
.card p{font-size:11.5px;line-height:22px;color:var(--muted);margin-top:6px;width:280px}
.card .more{font-family:"Cuprum",sans-serif;font-size:16px;color:var(--teal-dark);margin-top:10px}
.see-more{left:1063px;top:1641px;font-family:"Cuprum",sans-serif;font-size:16px}
.footer{left:35px;top:1934px;width:1144px;height:327px;background:linear-gradient(#3f7d75,#2b635c 60%,#25554f)}
.footer h5{position:absolute;font-family:"Cuprum",sans-serif;font-weight:400;font-size:21px;color:#fff}
.links{left:55px;top:74px;width:680px;display:grid;grid-template-columns:129px 164px 163px 224px;font-size:13.5px;color:#e6f0ee}
.links span{height:33px;line-height:33px;border-bottom:1px dashed #5d948c;padding-left:3px}
.social{left:767px;top:66px;display:flex;gap:10px}
.social i{display:block;width:32px;height:32px;border-radius:50%;background:#fff}
.copy{left:24px;top:250px;width:1098px;height:53px;background:#285a53;border-radius:4px;box-shadow:inset 0 0 3px #1b403b;font-size:11.5px;color:#e6f0ee;padding:17px 22px}
</style>
</head>
<body>
<div class="abs topbar">
  <span>EVENTS</span><span class="sep">|</span><span>NEWS EVENTS</span><span class="sep">|</span><span>SAVOUR</span><span class="sep">|</span><span>EVENT INTERNATIONAL ART SERIES</span><span class="sep">|</span><span>NSW EVENTS CALENDAR</span>
</div>

<div class="abs brand">Events</div>
<div class="abs slogan">your company slogan here</div>

<div class="abs account">
  <span><svg width="20" height="20" viewBox="0 0 20 20"><path d="M2 9h4v10H2zM7 9l4-7c2 0 2 2 1.5 4H18l-1.5 11H7z" fill="#1f4f49"/></svg>SIGN UP</span>
  <span><svg width="20" height="22" viewBox="0 0 20 22"><rect x="2" y="9" width="16" height="12" rx="2" fill="#1f4f49"/><path d="M5 9V6a5 5 0 0 1 10 0v3" fill="none" stroke="#1f4f49" stroke-width="2.5"/></svg>LOGIN</span>
  <span><svg width="26" height="22" viewBox="0 0 26 22"><circle cx="13" cy="6" r="5" fill="#1f4f49"/><path d="M2 22c0-7 5-10 11-10s11 3 11 10z" fill="#1f4f49"/></svg>MEMBER</span>
</div>
<div class="abs search">Enter Keyword here</div>
<div class="abs search-go">Go</div>

<div class="abs nav"><span>MAIN</span><span>POPULAR</span><span>EVENTS</span><span>HELP</span><span>SUPPORT</span><span>CONTACT</span></div>

<div class="abs hero" role="img" aria-label="Photo of a large conference hall with rows of chairs, a lit stage and projection screens"></div>
<div class="abs hero-arrow" style="left:22px;border-radius:0 24px 24px 0">‹</div>
<div class="abs hero-arrow" style="left:1156px;border-radius:24px 0 0 24px">›</div>

<div class="abs panel"></div>

<div class="abs filter">Date:<span class="field" style="width:152px"></span>Category:<span class="field" style="width:172px"></span>Show:<span class="field" style="width:152px"></span><span class="go">GO ›</span></div>

<div class="abs total">Total Events 30</div>

<div class="abs event" style="top:722px">
  <div class="photo" role="img" aria-label="Photo of a poker champion with stacks of prize money on stage" style="background:linear-gradient(#2a3a6a,#6a6a5a)"></div>
  <div class="body">
    <h3>Sydney Treasure Hunt on the Monorail</h3>
    <p>E-Commerce is a major progress in technology that has changed the way in which the customers now purchase information, products and the services. I</p>
    <div class="line">20 March 2012 &nbsp;until &nbsp;20 April 2012</div>
    <div class="line">Any Monorail Station</div>
    <div class="line">Chicago, IL</div>
    <div class="share">Share With &nbsp;<i style="background:#3aa3dc"></i><i style="background:#1f6fa8"></i><i style="background:#3b5ea0"></i></div>
  </div>
</div>

<div class="abs event" style="top:957px">
  <div class="photo" role="img" aria-label="Photo of a concert stage with green laser beams" style="background:linear-gradient(#0e2a2a,#1f5a5a 60%,#0b1a2a)"></div>
  <div class="body">
    <h3>18th Harbourside Art Biennial</h3>
    <p>E-Commerce is a major progress in technology that has changed the way in which the customers now purchase information, products and the services. I</p>
    <div class="line">20 March 2012 &nbsp;until &nbsp;20 April 2012</div>
    <div class="line">Any Monorail Station</div>
    <div class="line">Chicago, IL</div>
    <div class="share">Share With &nbsp;<i style="background:#3aa3dc"></i><i style="background:#1f6fa8"></i><i style="background:#3b5ea0"></i></div>
  </div>
</div>
<div class="abs divider" style="top:1163px"></div>

<div class="abs event" style="top:1212px">
  <div class="photo" role="img" aria-label="Photo of an award ceremony stage with winners lined up" style="background:linear-gradient(#2a2440,#6a2a3a 60%,#3a3050)"></div>
  <div class="body">
    <h3>The Permanent Exhibition</h3>
    <p>E-Commerce is a major progress in technology that has changed the way in which the customers now purchase information, products and the services. I</p>
    <div class="line">20 March 2012 &nbsp;until &nbsp;20 April 2012</div>
    <div class="line">Any Monorail Station</div>
    <div class="line">Chicago, IL</div>
    <div class="share">Share With &nbsp;<i style="background:#3aa3dc"></i><i style="background:#1f6fa8"></i><i style="background:#3b5ea0"></i></div>
  </div>
</div>
<div class="abs divider" style="top:1421px"></div>

<div class="abs event" style="top:1447px">
  <div class="photo" role="img" aria-label="Photo of an exhibition hall lit in purple and pink" style="background:linear-gradient(#2a1850,#8a2a8a 55%,#3a2050)"></div>
  <div class="body">
    <h3>Convict NewYork Exhibition</h3>
    <p>E-Commerce is a major progress in technology that has changed the way in which the customers now purchase information, products and the services. I</p>
    <div class="line">20 March 2012 &nbsp;until &nbsp;20 April 2012</div>
    <div class="line">Any Monorail Station</div>
    <div class="line">Chicago, IL</div>
    <div class="share">Share With &nbsp;<i style="background:#3aa3dc"></i><i style="background:#1f6fa8"></i><i style="background:#3b5ea0"></i></div>
  </div>
</div>
<div class="abs divider" style="top:1657px"></div>

<div class="abs event" style="top:1680px">
  <div class="photo" role="img" aria-label="Photo of a banquet room with round tables set in violet light" style="background:linear-gradient(#5a4aa0,#a59ad8 60%,#dcd6f0)"></div>
  <div class="body">
    <h3>Sydney Treasure Hunt on the Monorail</h3>
    <p>E-Commerce is a major progress in technology that has changed the way in which the customers now purchase information, products and the services. I</p>
    <div class="line">20 March 2012 &nbsp;until &nbsp;20 April 2012</div>
    <div class="line">Any Monorail Station</div>
    <div class="line">Chicago, IL</div>
    <div class="share">Share With &nbsp;<i style="background:#3aa3dc"></i><i style="background:#1f6fa8"></i><i style="background:#3b5ea0"></i></div>
  </div>
</div>

<div class="abs pager-rule"></div>
<div class="abs pager"><span class="on">1</span><span>2</span><span>3</span><span>4</span><span>5</span><span>6</span><span>7</span><span>8</span><span style="margin-left:6px">Next</span></div>

<div class="abs side"><h2>Popular Events</h2></div>

<div class="abs card" style="top:671px">
  <div class="photo" role="img" aria-label="Photo of a prize winner holding up cash" style="background:linear-gradient(#1a2a8a,#5a5aa0 50%,#2a3a9a)"></div>
  <h4>Event Name here</h4>
  <div class="meta">10 July to 20 Aug &nbsp;| &nbsp;&nbsp;Sydney &nbsp;NW</div>
  <p>Brightline eSolutions is specialized in handling advanced web projects and the ongoing proj-ects that require permanent maintenance and support .</p>
  <div class="more">learn more about this event ›</div>
</div>

<div class="abs card" style="top:996px">
  <div class="photo" role="img" aria-label="Photo of a party venue with large glowing balloons in blue light" style="background:linear-gradient(#2a3a9a,#6a7ad0 50%,#1a2060)"></div>
  <h4>Event Name here</h4>
  <div class="meta">10 July to 20 Aug &nbsp;| &nbsp;&nbsp;Sydney &nbsp;NW</div>
  <p>Brightline eSolutions is specialized in handling advanced web projects and the ongoing proj-ects that require permanent maintenance and support .</p>
  <div class="more">learn more about this event ›</div>
</div>

<div class="abs card" style="top:1320px">
  <div class="photo" role="img" aria-label="Photo of guests posing beside a celebration cake" style="background:linear-gradient(#6a3a30,#c8a898 55%,#5a3028)"></div>
  <h4>Event Name here</h4>
  <div class="meta">10 July to 20 Aug &nbsp;| &nbsp;&nbsp;Sydney &nbsp;NW</div>
  <p>Brightline eSolutions is specialized in handling advanced web projects and the ongoing proj-ects that require permanent maintenance and support .</p>
  <div class="more">learn more about this event ›</div>
</div>

<div class="abs see-more">SEE MORE..</div>

<footer class="abs footer">
  <h5 style="left:50px;top:22px">Quick Links</h5>
  <div class="abs links">
    <span>Hom page</span><span>Login</span><span>Support</span><span>Term &amp; Conditions of Use</span>
    <span>Events</span><span>FAQ</span><span>Add Events</span><span>Privacy Policy</span>
    <span>Popular</span><span>Login</span><span>Speical Events</span><span>Help</span>
    <span>News</span><span>Forgot Password</span><span>Contact info</span><span></span>
  </div>
  <h5 style="left:764px;top:22px">Connect with Us</h5>
  <div class="abs social"><i></i><i></i><i></i></div>
  <div class="abs copy">© 2012 Company Name &nbsp;| &nbsp;All right reserved &nbsp;| &nbsp;Policy Privacy</div>
</footer>
</body>
</html>
```